Kelumo.cn needs pages to be re-designed

www.kelumo.cn is our current new site which was launched in April.
We're a financial services website in the crowdfunding space in China to connect borrower's and lender's.

test.kelumo.cn is our test site
u: test
p: newtest
http://test.kelumo.cn/
http://test.kelumo.cn/user/accounts/new_lender
http://test.kelumo.cn/user/accounts/new_borrower
http://test.kelumo.cn/introductions/protection
http://test.kelumo.cn/introductions
http://test.kelumo.cn/introductions/kelumo_admin
http://test.kelumo.cn/introductions/contact
Some of the pages have pop-ups in the bloc's of the pages. Please click the links, to see more content.

User's currently criticize the website for being:
- Too Western looking
- Too simple, too little content
- Content NOT in the pop-ups are too simple
- Pictures are too big and too much blank space
- Relevant information is not there when needed
- The pictures are too generic

What we would like to do is re-design those pages with the same color scheme and style to be more compelling, efficient, non-intimidating and easy-to-use. Our audience is Ages 25-35 predominantly male investors.
We are looking for more ideas to make the content match the style, while bridging western and chinese design. Our ultimate goal is to increase registrants to the website and highlight our core competitive advantages.

Some competitors websites are:
www.fobuxiqi.com
www.tamev.com
www.zzzlendo.com

Reason: Not enough good designs that follow the prompt. Same style, better information layout!

Reason: Still have not received a design we're satisfied with

Reason: WE DONT WANT A COMPLETE REDESIGN OF PAGES . KEEP THE EXACT SAME COLOR AND STYLE - WE WANT CONTENT RE-DESIGN! THE BLOCS ARE TOO SIMPLE - WE WANT MORE CONTENT INSIDE.

Reason: no new designs

Reason: no new designs

Reason: other non-registered pages need to be re-designed

```html
<!DOCTYPE html>
<html lang="zh-CN">
<head>
<meta charset="utf-8">
<title>可路摩 Kelumo.cn · 安全保障</title>
<link href="https://fonts.googleapis.com/css2?family=Noto+Sans+SC:wght@400;500;700&display=swap" rel="stylesheet">
<style>
:root{
  --green:#5cb531;
  --green-dark:#3f8f1f;
  --blue:#2b8fd4;
  --ink:#3c3c3c;
  --text:#6b6b6b;
  --muted:#9a9a9a;
  --line:#dcdcdc;
  --bar:#4a4a4a;
  --bar-dark:#3a3a3a;
  --soft:#f4f5f6;
  --white:#ffffff;
}
*{margin:0;padding:0;box-sizing:border-box}
html,body{width:1200px;height:3408px;overflow:hidden}
body{font-family:"Noto Sans SC",sans-serif;color:var(--text);background:var(--white);position:relative}
a{text-decoration:none}
.abs{position:absolute}

/* header */
.site-header{position:absolute;left:0;top:0;width:1200px;height:82px;background:var(--white);border-bottom:1px solid var(--line)}
.brand{position:absolute;left:80px;top:18px;display:flex;align-items:center;gap:12px}
.brand-dot{width:44px;height:44px;border-radius:50%;background:var(--green)}
.brand-name{font-size:24px;font-weight:700;color:var(--ink);line-height:1}
.brand-sub{font-size:11px;color:var(--green);margin-top:4px}
.main-nav{position:absolute;right:70px;top:0;height:82px;display:flex}
.main-nav a{display:flex;flex-direction:column;align-items:center;justify-content:center;width:86px;font-size:14px;color:var(--ink);gap:6px}
.main-nav a.active{background:var(--green);color:var(--white)}
.main-nav i{width:20px;height:20px;border-radius:50%;border:2px solid currentColor;display:block}

/* hero */
.hero{position:absolute;left:0;top:82px;width:1200px;height:500px;background:linear-gradient(160deg,#e9edf1 0%,#cfd6dd 45%,#8d99a6 100%)}
.tab-bar{position:absolute;left:0;top:582px;width:1200px;height:62px;background:var(--bar);display:flex;padding-left:70px}
.tab-bar a{display:flex;align-items:center;gap:10px;color:var(--white);font-size:22px;padding:0 30px;border-right:1px solid #5e5e5e}
.tab-bar a:first-child{background:var(--bar-dark)}
.tab-bar i{width:26px;height:26px;border-radius:4px;background:var(--white);opacity:.9;display:block}

/* flow */
.flow{position:absolute;left:0;top:660px;width:1200px;height:790px}
.flow h2{position:absolute;top:30px;width:100%;text-align:center;font-size:28px;font-weight:500;color:var(--ink)}
.flow svg{position:absolute;left:0;top:0}
.flow-label{position:absolute;font-size:14px;color:var(--ink);white-space:nowrap}
.flow-label b{color:var(--blue);font-weight:700}
.flow-label.under{border-bottom:2px solid var(--blue);padding-bottom:4px}
.flow-pill{position:absolute;font-size:13px;color:var(--green);background:var(--white);padding:0 10px}
.flow-btn{position:absolute;left:520px;top:668px;width:160px;height:34px;border-radius:4px;background:var(--bar);color:var(--white);font-size:14px;display:flex;align-items:center;justify-content:center}
.partner{position:absolute;left:786px;top:540px;display:flex;align-items:center;gap:14px}
.partner .sq{width:40px;height:40px;border-radius:50%;background:var(--green)}
.partner .plus{font-size:30px;color:var(--muted)}
.partner-name{font-size:26px;font-weight:400;color:var(--ink);line-height:1}

/* blocks */
.features{position:absolute;left:0;top:1460px;width:1200px;height:1310px;background:var(--white)}
.block{position:absolute;width:500px}
.block-head{display:flex;align-items:center;gap:14px;height:60px;border-bottom:1px solid var(--line)}
.block-icon{width:46px;height:46px;border-radius:50%;background:var(--blue)}
.block-icon.green{background:var(--green)}
.block-icon.dark{background:var(--bar)}
.block-title{font-size:28px;color:var(--ink);font-weight:400}
.block-sub{font-size:15px;font-weight:700;color:var(--ink);margin:20px 0 10px}
.block-copy{font-size:13px;line-height:1.9;color:var(--text);width:220px}
.block-art{position:absolute}
.more{font-size:12px;color:var(--green);text-decoration:underline}
.stat-table{border-collapse:collapse;font-size:12px;color:var(--text)}
.stat-table td,.stat-table th{padding:6px 12px;border-bottom:1px solid var(--line);text-align:left;font-weight:400}
.stat-table th{color:var(--ink);font-weight:500}
.plain-name{font-size:18px;font-weight:400;color:var(--ink)}

/* safety box */
.safety{position:absolute;left:90px;top:2790px;width:1020px;height:300px;border:2px solid #c9dceb;border-radius:14px;background:var(--white)}
.safety-head{position:absolute;left:40px;top:-12px;display:flex;align-items:center;gap:14px;background:var(--white);padding:0 12px}
.safety-head .block-icon{width:52px;height:52px}
.safety-head span{font-size:26px;color:var(--ink)}
.safety-col{position:absolute;top:80px;width:460px;display:flex;align-items:center}
.safety-col h3{font-size:26px;font-weight:400;color:var(--ink);width:170px}
.safety-col ul{list-style:none;font-size:13px;color:var(--text);line-height:2}
.safety-col li::before{content:"";display:inline-block;width:7px;height:7px;background:var(--green);margin-right:10px;vertical-align:middle}
.safety-col .more{display:block;margin-top:6px;margin-left:17px}

/* cta */
.cta{position:absolute;left:490px;top:3128px;width:220px;height:60px;border-radius:30px;background:var(--green);color:var(--white);display:flex;align-items:center;justify-content:center;gap:12px;font-size:24px;font-weight:500}
.cta i{width:28px;height:28px;border-radius:50%;border:3px solid var(--white);display:block}

/* partners footer */
.partners{position:absolute;left:0;top:3220px;width:1200px;height:120px;background:var(--white);border-top:1px solid var(--line)}
.partners .cap{position:absolute;left:90px;top:14px;font-size:12px;color:var(--ink)}
.partner-row{position:absolute;left:90px;top:48px;display:flex;align-items:center;gap:34px}
.badge{height:34px;border-radius:4px;background:#d9dde1}
.partner-row .plain-name{font-size:16px}
.site-footer{position:absolute;left:0;top:3340px;width:1200px;height:68px;background:#e4e6e8;display:flex;align-items:center;padding:0 90px;gap:50px;font-size:13px;color:var(--text)}
.site-footer .brand-dot{width:30px;height:30px;background:#b9bec3}
.foot-icons{margin-left:auto;display:flex;gap:18px}
.foot-icons i{width:26px;height:26px;border-radius:50%;background:#bfc4c8;display:block}
</style>
</head>
<body>

<header class="site-header">
  <div class="brand">
    <div class="brand-dot"></div>
    <div><div class="brand-name">可路摩</div><div class="brand-sub">kelumo.cn</div></div>
  </div>
  <nav class="main-nav">
    <a href="#"><i></i>首页</a>
    <a href="#" class="active"><i></i>保障</a>
    <a href="#"><i></i>借款</a>
    <a href="#"><i></i>投资</a>
    <a href="#"><i></i>登录 ▾</a>
  </nav>
</header>

<div class="hero" role="img" aria-label="Photo of hands sketching a light bulb idea and a house on paper"></div>

<nav class="tab-bar">
  <a href="#"><i></i>风控</a>
  <a href="#"><i></i>保护金</a>
  <a href="#"><i></i>分散</a>
  <a href="#"><i></i>资金安全</a>
  <a href="#"><i></i>责任</a>
</nav>

<section class="flow">
  <h2>6 標題範例</h2>
  <svg width="1200" height="790" viewBox="0 0 1200 790" fill="none">
    <g stroke="#5cb531" stroke-width="4">
      <path d="M150 260 V130 H1050 V150"/>
    </g>
    <g stroke="#4a4a4a" stroke-width="3">
      <path d="M150 260 V520 H600"/>
      <path d="M150 390 H830"/>
      <path d="M150 460 H600"/>
      <path d="M870 250 H930 M930 210 V400 M930 210 H980 M930 300 H980 M930 390 H980"/>
    </g>
    <g stroke="#5cb531" stroke-width="3">
      <path d="M410 250 H870 V300"/>
    </g>
    <g fill="#8d8d8d">
      <path d="M590 460 h20 v18 h12 l-22 22 l-22 -22 h12z"/>
      <path d="M590 540 h20 v18 h12 l-22 22 l-22 -22 h12z"/>
      <path d="M590 610 h20 v18 h12 l-22 22 l-22 -22 h12z"/>
    </g>
    <circle cx="150" cy="262" r="18" fill="#9a9a9a"/>
    <g fill="#9a9a9a">
      <circle cx="1000" cy="210" r="14"/><circle cx="1000" cy="300" r="14"/><circle cx="1000" cy="390" r="14"/>
    </g>
    <path d="M120 720 H560 M640 720 H1080" stroke="#2b8fd4" stroke-width="2"/>
  </svg>
  <div class="flow-pill" style="left:560px;top:120px">標題範例</div>
  <div class="flow-label" style="left:175px;top:272px">示例文本</div>
  <div class="flow-label under" style="left:330px;top:214px"><b>2.</b> 每年: 示例文本每</div>
  <div class="flow-label under" style="left:870px;top:160px"><b>1.</b> 每年: 示例文本每</div>
  <div class="flow-label" style="left:1022px;top:200px">示例文本</div>
  <div class="flow-label" style="left:1022px;top:290px">示例文本</div>
  <div class="flow-label" style="left:1022px;top:380px">示例文本</div>
  <div class="flow-label" style="left:500px;top:432px">標題範例標題範例</div>
  <div class="flow-label" style="left:640px;top:500px"><b>3.</b> 每年: 標題範例標題範例</div>
  <div class="flow-label" style="left:640px;top:580px"><b>4.</b> 每年: 標題範例</div>
  <div class="partner"><div class="sq"></div><span class="plus">+</span><span class="partner-name">Brenmar</span></div>
  <div class="flow-btn">了解详情</div>
  <div class="flow-label" style="left:270px;top:738px"><b>5.</b> 每年: 示例文本每年標題範例標題範例</div>
  <div class="flow-label" style="left:650px;top:738px"><b>6.</b> 每年: 標題範例標題範例標題範例</div>
</section>

<section class="features">
  <article class="block" style="left:90px;top:20px">
    <div class="block-head"><div class="block-icon"></div><h3 class="block-title">1, 风控</h3></div>
    <p class="block-sub">樣本標題樣本標題</p>
    <p class="block-copy">借款人须通过身份、收入、信用等多重审核，平台以严格标准筛选项目，确保每一笔借款真实可靠，降低违约风险，保障投资人权益与资金安全，让您投资更安心，收益更稳定可期。</p>
    <svg class="block-art" style="left:260px;top:90px" width="220" height="300" viewBox="0 0 220 300">
      <path d="M0 10 H220 L196 60 H24Z" fill="#c5e6f7"/>
      <path d="M26 66 H194 L172 112 H48Z" fill="#8fd0ef"/>
      <path d="M50 118 H170 L152 160 H68Z" fill="#4fb3e3"/>
      <path d="M70 166 H150 L136 200 H84Z" fill="#2b8fd4"/>
      <path d="M86 206 H134 L124 236 H96Z" fill="#1f6fa8"/>
      <rect x="98" y="242" width="24" height="40" fill="#5cb531"/>
    </svg>
  </article>

  <article class="block" style="left:620px;top:20px">
    <div class="block-head"><div class="block-icon"></div><h3 class="block-title">2, 分散</h3></div>
    <p class="block-sub">樣本標題樣本標題</p>
    <p class="block-copy">分散投资到多个借款项目，单笔违约对整体收益影响极小，风险被有效摊薄，收益更平稳。</p>
    <svg class="block-art" style="left:0;top:200px" width="500" height="250" viewBox="0 0 500 250">
      <g stroke="#9a9a9a" stroke-width="2" fill="none">
        <path d="M40 130 H120 M120 20 V240 M120 20 H330 M120 95 H330 M120 170 H330 M120 240 H330"/>
      </g>
      <g fill="#8d8d8d">
        <circle cx="40" cy="120" r="14"/>
        <circle cx="350" cy="20" r="11"/><circle cx="350" cy="95" r="11"/><circle cx="350" cy="170" r="11"/><circle cx="350" cy="240" r="11"/>
      </g>
      <g font-size="13" fill="#2b8fd4" font-family="Noto Sans SC, sans-serif">
        <text x="372" y="25">¥200</text><text x="372" y="100">¥200</text><text x="372" y="175">¥200</text><text x="372" y="245">¥200</text>
        <text x="20" y="160" fill="#6b6b6b">示例文本</text><text x="22" y="178">¥1000</text>
      </g>
    </svg>
  </article>

  <article class="block" style="left:90px;top:510px">
    <div class="block-head"><div class="block-icon green"></div><h3 class="block-title">3, 保护金</h3></div>
    <p class="block-copy" style="margin-top:18px">平台提取风险保证金专户管理，借款逾期时优先垫付本息，保护投资人利益，减少资金损失。</p>
    <svg class="block-art" style="left:300px;top:72px" width="170" height="170" viewBox="0 0 170 170">
      <circle cx="85" cy="85" r="62" fill="none" stroke="#5cb531" stroke-width="34"/>
      <circle cx="85" cy="85" r="62" fill="none" stroke="#2b8fd4" stroke-width="34" stroke-dasharray="120 390" transform="rotate(-90 85 85)"/>
      <circle cx="85" cy="85" r="62" fill="none" stroke="#4a4a4a" stroke-width="34" stroke-dasharray="50 390" stroke-dashoffset="-120" transform="rotate(-90 85 85)"/>
    </svg>
    <table class="stat-table abs" style="left:0;top:268px;width:480px">
      <tr><th>期限</th><th>保障比例</th><th>示例文本</th><th>示例文本</th></tr>
      <tr><td>1-3月</td><td>100% 本息</td><td>示例文本</td><td>示例</td></tr>
      <tr><td>3-6月</td><td>100% 本金</td><td>示例文本</td><td>示例</td></tr>
      <tr><td>6-12月</td><td>100% 本金</td><td>示例文本</td><td>示例</td></tr>
    </table>
    <a class="more abs" style="left:150px;top:396px" href="#">了解保护金详情</a>
  </article>

  <article class="block" style="left:620px;top:510px">
    <div class="block-head"><div class="block-icon dark"></div><h3 class="block-title">4, 将您的风险</h3></div>
    <p class="block-sub">年示例文本每年示例文本</p>
    <svg class="block-art" style="left:0;top:120px" width="500" height="290" viewBox="0 0 500 290">
      <g stroke="#9a9a9a" stroke-width="2" fill="none">
        <path d="M60 60 L250 150 L440 60 M60 240 L250 150 L440 240 M250 60 V240"/>
      </g>
      <g fill="#8d8d8d"><circle cx="60" cy="60" r="14"/><circle cx="440" cy="60" r="14"/><circle cx="60" cy="240" r="14"/><circle cx="440" cy="240" r="14"/></g>
      <circle cx="250" cy="150" r="36" fill="#5cb531"/>
      <rect x="226" y="40" width="48" height="28" rx="4" fill="#d9dde1"/>
      <g font-size="12" fill="#6b6b6b" font-family="Noto Sans SC, sans-serif">
        <text x="30" y="95">投资人</text><text x="410" y="95">借款人</text><text x="30" y="275">保护金</text><text x="410" y="275">合作方</text>
        <text x="286" y="58" fill="#3c3c3c">Brenmar</text>
      </g>
    </svg>
  </article>

  <article class="block" style="left:90px;top:930px">
    <div class="block-head"><div class="block-icon"></div><h3 class="block-title">5, 资金安全</h3></div>
    <p class="block-sub">资金安全</p>
    <p class="block-copy">投资资金由第三方托管账户管理，平台不触碰用户资金，借贷双方直接交易，流程透明可查。</p>
    <svg class="block-art" style="left:260px;top:80px" width="220" height="270" viewBox="0 0 220 270">
      <g stroke="#9a9a9a" stroke-width="2" fill="none"><path d="M110 30 V240 M60 130 H160"/></g>
      <circle cx="110" cy="30" r="14" fill="#8d8d8d"/>
      <rect x="80" y="110" width="60" height="40" rx="4" fill="#2b8fd4"/>
      <circle cx="110" cy="240" r="14" fill="#8d8d8d"/>
    </svg>
  </article>

  <article class="block" style="left:620px;top:930px">
    <div class="block-head"><div class="block-icon"></div><h3 class="block-title">6, 将您的风险</h3></div>
    <p class="block-sub">资金安全</p>
    <p class="block-copy">服务器由专业云服务商运维，数据多地备份，加密传输，全天候监控，保障账户与信息安全。</p>
    <div class="block-art" style="left:270px;top:80px">
      <div class="plain-name">NetHaven Cloud</div>
      <div style="font-size:12px;color:var(--text);margin:6px 0 14px">资金托管账户</div>
      <div class="badge" style="width:110px;margin-bottom:12px"></div>
      <div class="badge" style="width:110px;margin-bottom:12px"></div>
      <div class="badge" style="width:110px"></div>
    </div>
  </article>
</section>

<section class="safety">
  <div class="safety-head"><div class="block-icon"></div><span>资金安全</span></div>
  <div class="safety-col" style="left:30px">
    <h3>将您的风险</h3>
    <div>
      <ul>
        <li>项目审核严格分级管理</li><li>资金第三方托管保障</li><li>风险保证金优先垫付</li>
        <li>分散投资降低风险</li><li>信息加密安全传输</li><li>合作机构共同担保</li>
      </ul>
      <a class="more" href="#">了解详情</a>
    </div>
  </div>
  <div class="safety-col" style="left:530px">
    <h3>将您的</h3>
    <div>
      <ul>
        <li>借款用途真实可查询</li><li>逾期催收专业团队</li><li>账户资金实时可见</li>
        <li>收益每月按时到账</li><li>客服全天在线答疑</li><li>合同电子签章存证</li>
      </ul>
      <a class="more" href="#">了解详情</a>
    </div>
  </div>
</section>

<a class="cta" href="#"><i></i>开始投资</a>

<section class="partners">
  <p class="cap">合作伙伴</p>
  <div class="partner-row">
    <div class="badge" style="width:110px"></div>
    <span class="plain-name">NetHaven Cloud</span>
    <div class="badge" style="width:140px"></div>
    <div class="badge" style="width:120px"></div>
    <div class="badge" style="width:120px"></div>
    <div class="badge" style="width:150px"></div>
  </div>
</section>

<footer class="site-footer">
  <div style="display:flex;align-items:center;gap:10px"><div class="brand-dot"></div><span>可路摩</span></div>
  <span>显示的服务 ▾</span>
  <div class="foot-icons"><i></i><i></i><i></i><i></i></div>
</footer>

</body>
</html>
```